Investment company needing business card

We are wanting a business card which looks sharp and easy on the eye. We are thinking of having a business card with the logo embossed on it, to really make it stand out. We will only have a small amount of information of the business card, person's name, position, email address and phone number

Contact Information for Business Card

Danielle Frost
Executive Assistant
+64 21 473 5162
danielf@harwickpartners.co.nz

Requirements
Must have
• Embossed logo
Should not have
• Not to be busy

```html
<!DOCTYPE html>
<html lang="en">
<head>
<meta charset="utf-8">
<title>Harwick Partners — Business Card</title>
<link href="https://fonts.googleapis.com/css2?family=Michroma&family=Lato:wght@400&display=swap" rel="stylesheet">
<style>
  :root {
    --brand-green: #25b573;
    --brand-green-light: rgba(255, 255, 255, 0.16);
    --ink-grey: #5f5f5f;
    --text-dark: #2f2f2f;
    --card-white: #ffffff;
    --emboss-grey: #efefef;
    --backdrop: #3a3a3a;
  }
  * { box-sizing: border-box; margin: 0; padding: 0; }
  html, body { width: 1200px; height: 1108px; overflow: hidden; }
  body {
    background: var(--backdrop);
    display: flex;
    flex-direction: column;
    align-items: center;
    justify-content: center;
    gap: 48px;
    font-family: "Lato", sans-serif;
  }
  .card {
    position: relative;
    width: 840px;
    height: 480px;
    overflow: hidden;
    box-shadow: 0 12px 30px rgba(0, 0, 0, 0.35);
  }
  .card--front { background: var(--card-white); }
  .card--back {
    background: var(--brand-green);
    display: flex;
    align-items: center;
    justify-content: center;
  }
  .emboss-mark {
    position: absolute;
    border-radius: 60px;
  }
  .card--front .emboss-mark {
    width: 340px; height: 340px;
    right: -40px; bottom: -90px;
    background: var(--emboss-grey);
  }
  .card--back .emboss-mark {
    width: 360px; height: 360px;
    right: -50px; bottom: -110px;
    background: var(--brand-green-light);
  }
  .wordmark {
    position: relative;
    display: flex;
    align-items: center;
    gap: 18px;
    font-family: "Michroma", sans-serif;
    letter-spacing: 0.04em;
  }
  .wordmark__square { width: 44px; height: 44px; }
  .card--front .wordmark {
    position: absolute;
    top: 64px; left: 64px;
    color: var(--brand-green);
    font-size: 34px;
  }
  .card--front .wordmark__square { background: var(--ink-grey); }
  .card--back .wordmark { color: var(--card-white); font-size: 40px; }
  .card--back .wordmark__square { background: var(--card-white); width: 52px; height: 52px; }
  .contact {
    position: absolute;
    left: 64px; top: 230px;
    color: var(--text-dark);
  }
  .contact__name {
    font-family: "Michroma", sans-serif;
    color: var(--brand-green);
    font-size: 28px;
    letter-spacing: 0.04em;
    text-transform: uppercase;
  }
  .contact__role { font-size: 22px; margin: 6px 0 22px; color: var(--ink-grey); }
  .contact__line {
    display: flex; align-items: center; gap: 12px;
    font-size: 21px; margin-bottom: 10px;
  }
  .contact__icon { width: 18px; height: 18px; fill: var(--brand-green); flex: none; }
</style>
</head>
<body>
  <section class="card card--front" aria-label="Business card front">
    <div class="emboss-mark" aria-hidden="true"></div>
    <div class="wordmark">
      <span class="wordmark__square" aria-hidden="true"></span>
      <span class="wordmark__name">HARWICK PARTNERS</span>
    </div>
    <div class="contact">
      <p class="contact__name">Danielle Frost</p>
      <p class="contact__role">Executive Assistant</p>
      <p class="contact__line">
        <svg class="contact__icon" viewBox="0 0 24 24" aria-hidden="true"><path d="M6.6 10.8a15.1 15.1 0 0 0 6.6 6.6l2.2-2.2a1 1 0 0 1 1-.25 11.4 11.4 0 0 0 3.6.57 1 1 0 0 1 1 1V20a1 1 0 0 1-1 1A17 17 0 0 1 3 4a1 1 0 0 1 1-1h3.5a1 1 0 0 1 1 1c0 1.25.2 2.45.57 3.57a1 1 0 0 1-.25 1z"/></svg>
        <span>+64 21 473 5162</span>
      </p>
      <p class="contact__line">
        <svg class="contact__icon" viewBox="0 0 24 24" aria-hidden="true"><path d="M2 5h20v14H2z M4 7v.4l8 5.2 8-5.2V7z" fill-rule="evenodd"/></svg>
        <span>danielf@harwickpartners.co.nz</span>
      </p>
    </div>
  </section>

  <section class="card card--back" aria-label="Business card back">
    <div class="emboss-mark" aria-hidden="true"></div>
    <div class="wordmark">
      <span class="wordmark__square" aria-hidden="true"></span>
      <span class="wordmark__name">HARWICK PARTNERS</span>
    </div>
  </section>
</body>
</html>
```